Roadside building business signage for a holistic health clinic.

Replace signs as shown in the attached file. They are perforated stickers that go on the windows as shown. Looking for something that has our logo and says the name of the practice with logo (Fernridge Health & Wellness) also boldly says Acupuncture, IV Vitamins, and Holistic Health.
Possibly our phone number as well 318-562-7041
Updates

Please don't use pink except the logo. Earthy, organic tone colors appreciated.

Need of eye catching window signage of a holistic clinic on a brick building. Pink, purple, sage green, white color. Logo is pink on a white background. Please don't overload with too much pink. Words to include are "Fernridge Health and Wellness(name of business)", "Direct Primary Care", " Medical acupuncture", "IV Vitamin Therapy", "fernridgecareclinic.example","318-562-7041".

Target Market(s)

People will see in their cars passing by the building. Busy roadside so need to be visible while passing in fast speed.

Industry/Entity Type

Health & Wellness

Font styles to use
Sans Serif

Colors

Designer to choose colors to be used in the design.

Requirements
Must have
• On sign must have words Holistic Medicine, Medical Acupuncture, Direct Primary Care and IV vitamins.
Nice to have
• Simple, minimalistic, artistic yet has clear message. White, Black, Violet, Pink (logo), Dark green, Sage green.
Should not have
• Bold colors (red, yellow, blue), same tone colors. Blue waves on the current signage (uploaded file) must go.

```html
<!DOCTYPE html>
<html lang="en">
<head>
<meta charset="utf-8">
<title>Fernridge Health &amp; Wellness – Window Signage</title>
<link href="https://fonts.googleapis.com/css2?family=Montserrat:wght@500;600;700&display=swap" rel="stylesheet">
<style>
  :root {
    --canvas-bg: #e2e2e2;
    --forest: #0d4d3f;
    --logo-pink: #d6307f;
    --sage: #9db59a;
    --sage-dark: #6f8f70;
    --sage-mist: #e7efe4;
    --white: #ffffff;
    --ink: #1c1c1c;
  }
  * { margin: 0; padding: 0; box-sizing: border-box; }
  html, body { width: 800px; height: 1200px; overflow: hidden; }
  body {
    background: var(--canvas-bg);
    font-family: "Montserrat", Arial, sans-serif;
    position: relative;
  }
  .sign {
    position: absolute;
    top: 431px;
    width: 337px;
    height: 337px;
    overflow: hidden;
    box-shadow: 0 2px 6px rgba(0,0,0,0.12);
  }
  .sign--services { left: 46px; background: linear-gradient(160deg, var(--white) 30%, var(--sage-mist) 70%, var(--white) 100%); }
  .sign--brand { left: 408px; background: var(--forest); }

  .sign__art { position: absolute; inset: 0; width: 100%; height: 100%; }

  .brand-mark {
    position: absolute;
    left: 0; right: 0;
    text-align: center;
    color: var(--white);
    font-weight: 500;
  }
  .brand-mark__dot {
    display: block;
    margin: 0 auto;
    border-radius: 50%;
    background: var(--logo-pink);
  }
  .brand-mark__name { display: block; text-transform: uppercase; line-height: 1; }
  .brand-mark__tag { display: block; text-transform: uppercase; line-height: 1; }

  .sign--services .brand-mark { top: 22px; }
  .sign--services .brand-mark__dot { width: 44px; height: 44px; margin-bottom: 12px; }
  .sign--services .brand-mark__name { font-size: 21px; letter-spacing: 3px; }
  .sign--services .brand-mark__tag { font-size: 7.5px; letter-spacing: 3px; margin-top: 6px; }

  .sign--brand .brand-mark { top: 50px; }
  .sign--brand .brand-mark__dot { width: 104px; height: 104px; margin-bottom: 20px; }
  .sign--brand .brand-mark__name { font-size: 34px; letter-spacing: 4px; }
  .sign--brand .brand-mark__tag { font-size: 11px; letter-spacing: 5px; margin-top: 9px; }

  .contact {
    position: absolute;
    left: 0; right: 0;
    top: 262px;
    text-align: center;
    color: var(--white);
  }
  .contact__phone { display: block; font-size: 20px; font-weight: 700; letter-spacing: 1px; }
  .contact__web { display: block; font-size: 13px; font-weight: 500; margin-top: 8px; color: var(--sage); letter-spacing: 0.5px; }

  .services {
    position: absolute;
    left: 30px;
    top: 170px;
    list-style: none;
  }
  .services__item {
    display: flex;
    align-items: center;
    height: 37px;
    font-weight: 700;
    font-size: 19px;
    color: var(--ink);
  }
  .services__icon {
    width: 30px; height: 30px;
    border-radius: 50%;
    background: var(--sage-dark);
    border: 2px solid var(--white);
    box-shadow: 0 0 0 1.5px var(--sage-dark);
    margin-right: 11px;
    flex: none;
  }
</style>
</head>
<body>

  <section class="sign sign--services" aria-label="Services window sign">
    <svg class="sign__art" viewBox="0 0 661 661" aria-hidden="true">
      <path d="M0 0 H661 V170 C600 290 480 330 360 330 C200 330 60 240 0 90 Z" fill="var(--forest)"/>
      <path d="M400 328 C520 322 620 262 661 160 V215 C610 295 520 332 400 328 Z" fill="var(--sage-dark)"/>
      <rect x="0" y="642" width="661" height="19" fill="var(--forest)"/>
    </svg>
    <svg class="sign__art" viewBox="0 0 661 661" role="img" aria-label="Eucalyptus sprig illustration">
      <path d="M661 0 V230 C625 250 575 225 555 190 C545 145 575 90 610 40 C628 15 645 0 661 0 Z" fill="var(--sage)" opacity="0.9"/>
    </svg>

    <div class="brand-mark">
      <span class="brand-mark__dot"></span>
      <span class="brand-mark__name">Fernridge</span>
      <span class="brand-mark__tag">Health &amp; Wellness</span>
    </div>

    <ul class="services">
      <li class="services__item"><span class="services__icon" role="img" aria-label="Acupuncture icon"></span>Medical Acupuncture</li>
      <li class="services__item"><span class="services__icon" role="img" aria-label="Vitamins icon"></span>IV Vitamins</li>
      <li class="services__item"><span class="services__icon" role="img" aria-label="Holistic care icon"></span>Holistic Medicine</li>
      <li class="services__item"><span class="services__icon" role="img" aria-label="Primary care icon"></span>Direct Primary Care</li>
    </ul>
  </section>

  <section class="sign sign--brand" aria-label="Brand window sign">
    <div class="brand-mark">
      <span class="brand-mark__dot"></span>
      <span class="brand-mark__name">Fernridge</span>
      <span class="brand-mark__tag">Health &amp; Wellness</span>
    </div>
    <div class="contact">
      <span class="contact__phone">318-562-7041</span>
      <span class="contact__web">fernridgecareclinic.example</span>
    </div>
  </section>

</body>
</html>
```